Exclusive beauty salon needs a price list or services booklet

I need a new very attractive flyer for my beauty salon, containing information on the different services and their prices.
In attachment you can find a pdf of the "old" one, but I'd love to have a beautifully designed new one!
I'd love to have a booklet in format 148 x 148 mm, or in US format, containing 12 or 16 pages, but if you can offer other nice looking designs they are welcome!
The services that need to come in the booklet with their prices can all be found on my website: www.atelierverano.be, starting with
Gelaatsverzorging
Wimperverlenging
Suikerontharing
Wimperlifting
Permanente Make Up
Airbrush Tanning

Target Market(s)

woman from 20 to 89 years old

Industry/Entity Type

Beauty Salon

Font styles to use
Sans Serif

Colors

Designer to choose colors to be used in the design.

Requirements
Must have
• a classy nice look, it must contain details about the services from my beauty salon and their prices, and nice pictures.
• The Names, prices and explanations of the services can easily be found on my website: www.atelierverano.be
Nice to have
• In attachment you can find the "old" price list in pdf, what I need now is a "new booklet" with the new logo and updated services price list.
• I need a very nice and attractive looking booklet, classy chique, Paris chique, looking very expensive.
Should not have
• Not too much colors, not too curly, but still feminine

```html
<!DOCTYPE html>
<html lang="nl">
<head>
<meta charset="utf-8">
<title>Atelier Verano – Over mij</title>
<link rel="stylesheet" href="https://fonts.googleapis.com/css2?family=Source+Sans+3:ital,wght@1,300;1,400&display=swap">
<style>
  :root {
    --paper: #ffffff;
    --stone: #a4a4a8;
    --ink-light: #ffffff;
  }
  * { margin: 0; padding: 0; box-sizing: border-box; }
  html, body {
    width: 1200px;
    height: 868px;
    overflow: hidden;
    background: var(--paper);
  }
  .page {
    position: relative;
    width: 1200px;
    height: 868px;
  }
  .panel {
    position: absolute;
    left: 34px;
    top: 34px;
    width: 1128px;
    height: 797px;
    background: var(--stone);
  }
  .intro-frame {
    position: absolute;
    left: 278px;
    top: 209px;
    width: 641px;
    height: 444px;
    border: 1.5px solid var(--ink-light);
  }
  .intro-text {
    position: absolute;
    left: 316px;
    top: 280px;
    width: 564px;
    font-family: "Source Sans 3", "Myriad Pro", sans-serif;
    font-style: italic;
    font-weight: 400;
    font-size: 21px;
    line-height: 27.5px;
    color: var(--ink-light);
  }
  .intro-text .line {
    display: block;
    text-align: justify;
    text-align-last: justify;
  }
  .intro-text .line.end {
    text-align-last: left;
  }
  .intro-text p + p {
    margin-top: 27.5px;
  }
</style>
</head>
<body>
  <main class="page">
    <div class="panel"></div>
    <div class="intro-frame"></div>
    <section class="intro-text">
      <p>
        <span class="line">Al meer dan 5 jaar lang sta ik met evenveel passie en</span>
        <span class="line">enthousiasme klaar om mijn klanten met de glimlach</span>
        <span class="line">te ontvangen. Mijn specialiteiten zijn gelaatsver-</span>
        <span class="line">zorgingen met de kwalitatieve producten van Velouria,</span>
        <span class="line">wimperextensions, suikerontharing en Permanente</span>
        <span class="line end">Make Up.</span>
      </p>
      <p>
        <span class="line">Ik volg regelmatig bijscholingen om bij te blijven met</span>
        <span class="line end">de nieuwste trends.</span>
      </p>
    </section>
  </main>
</body>
</html>
```